Founder / concept developer needs business card // Consultant needs VCARD

I need a business card for me as a founding consultant in Berlin. I advise entrepreneurs, especially in the design of business ideas, business plans or financing applications. More information about this in the annexes. My USP: I design / structure complex ideas and projects convincingly so that my client is successful. I want to communicate professionalism, effectiveness and clarity. Colors like from the range BLACK-GRAY-GREEN. I am 27 years old, I have studied business for 7 years. Attachments: - Business card design (only idea, do not focus on it) - Website screenshot (only idea, do not focus on it)

Target Market(s)

Target group: Founder (20-50 yrs, m / w, needy, in "break-up phase") and CONTRACTOR / "financier" (30-55 yrs, m / w, often public service "routine-oriented"). The foundations are in quite different industries: digital, craft, tourism, retail, services, etc. Almost all German.

Industry/Entity Type

Consultant

Contact Information for Business Card

Lukas Brennwald
M. Sc., International Business Administration
Gründungsberater, Konzeptentwickler
www.kelvoran-mitrel.de
Postfach-Zugang@kelvoran.de
Tel. 0481 294 3172

Colors

Designer to choose colors to be used in the design.

Requirements
Must have
• Professionalism, persuasiveness, clarity
Nice to have
• memorability
Should not have
• Schnörkelei

```html
<!DOCTYPE html>
<html lang="de">
<head>
<meta charset="utf-8">
<title>Lukas Brennwald – Visitenkarte</title>
<link rel="stylesheet" href="https://fonts.googleapis.com/css2?family=Poppins:wght@500;600&family=Work+Sans:wght@400;500&display=swap">
<style>
  :root {
    --green: #3fa94a;
    --green-dark: #2f8f3a;
    --green-light: #6cc472;
    --ink: #3a3a3a;
    --grey: #6b6b6b;
    --line-grey: #4a4a4a;
    --paper: #ffffff;
    --backdrop: #2b2b2b;
  }
  * { box-sizing: border-box; margin: 0; padding: 0; }
  html, body { width: 1200px; height: 930px; overflow: hidden; }
  body {
    background: var(--backdrop);
    font-family: "Work Sans", sans-serif;
    position: relative;
  }
  .card {
    position: absolute;
    left: 280px;
    width: 640px;
    height: 400px;
    border-radius: 22px;
    overflow: hidden;
  }
  .card-back { top: 45px; background: var(--green); }
  .card-front { top: 485px; background: var(--paper); }

  .cube-mark {
    position: absolute;
    border-radius: 6px;
  }
  .card-back .cube-mark {
    left: 250px; top: 120px; width: 140px; height: 140px;
    background: linear-gradient(135deg, #7fcf86, #2e7d35);
  }
  .card-back .back-url {
    position: absolute; left: 0; right: 0; bottom: 36px;
    text-align: center; color: var(--paper);
    font-size: 15px; letter-spacing: 0.3px;
  }

  .card-front .cube-mark {
    left: 62px; top: 95px; width: 170px; height: 170px;
    background: linear-gradient(135deg, #6cc472, #3a7f40 70%, #555);
  }
  .divider {
    position: absolute; left: 282px; top: 62px;
    width: 2px; height: 190px; background: var(--green);
  }
  .details { position: absolute; left: 310px; top: 58px; width: 310px; }
  .name {
    font-family: "Poppins", sans-serif; font-weight: 600;
    font-size: 27px; color: var(--green); line-height: 1.1;
  }
  .degree { font-size: 12.5px; color: var(--grey); margin-top: 4px; line-height: 1.35; }
  .role { font-size: 14px; color: var(--ink); margin-top: 10px; line-height: 1.35; }
  .contacts { list-style: none; margin-top: 12px; }
  .contacts li {
    display: flex; align-items: center; gap: 9px;
    font-size: 14px; color: var(--ink); line-height: 1.55;
  }
  .contacts svg { width: 11px; height: 11px; flex: none; }
  .wave { position: absolute; left: 0; top: 0; width: 640px; height: 400px; }
</style>
</head>
<body>

<section class="card card-back">
  <div class="cube-mark" role="img" aria-label="Logo-Illustration: grüner Würfel"></div>
  <p class="back-url">www.kelvoran-mitrel.de</p>
</section>

<section class="card card-front">
  <svg class="wave" viewBox="0 0 640 400" aria-hidden="true">
    <path d="M0 384 C180 378 310 360 410 322 C490 292 565 282 640 278 L640 400 L0 400 Z" fill="var(--green)"/>
    <path d="M0 377 C180 371 310 353 410 315 C490 285 565 275 640 271" fill="none" stroke="var(--line-grey)" stroke-width="3"/>
    <path d="M0 381 C180 375 310 357 410 319 C490 289 565 279 640 275" fill="none" stroke="var(--paper)" stroke-width="2"/>
  </svg>

  <div class="cube-mark" role="img" aria-label="Logo-Illustration: grüner Würfel"></div>
  <div class="divider"></div>

  <div class="details">
    <h1 class="name">Lukas Brennwald</h1>
    <p class="degree">M. Sc.,<br>International Business Administration</p>
    <p class="role">Gründungsberater,<br>Konzeptentwickler</p>
    <ul class="contacts">
      <li>
        <svg viewBox="0 0 12 12"><path d="M2.5 1 L4.5 1 L5.3 3.4 L4 4.4 C4.6 5.8 6.2 7.4 7.6 8 L8.6 6.7 L11 7.5 L11 9.5 C11 10.4 10.4 11 9.5 11 C5 11 1 7 1 2.5 C1 1.6 1.6 1 2.5 1 Z" fill="var(--green)"/></svg>
        0481 294 3172
      </li>
      <li>
        <svg viewBox="0 0 12 12"><rect x="1" y="2.5" width="10" height="7" rx="1" fill="none" stroke="var(--green)" stroke-width="1.3"/><path d="M1.5 3 L6 6.5 L10.5 3" fill="none" stroke="var(--green)" stroke-width="1.3"/></svg>
        Postfach-Zugang@kelvoran.de
      </li>
      <li>
        <svg viewBox="0 0 12 12"><circle cx="6" cy="6" r="5" fill="none" stroke="var(--green)" stroke-width="1.3"/><path d="M1 6 H11 M6 1 C3.5 3.5 3.5 8.5 6 11 M6 1 C8.5 3.5 8.5 8.5 6 11" fill="none" stroke="var(--green)" stroke-width="1"/></svg>
        www.kelvoran-mitrel.de
      </li>
    </ul>
  </div>
</section>

</body>
</html>
```